Public Speaking Book for aspiring, ambitious speakers

I'm looking for a 6x9 book cover (Brivora standard) as well as ebook and audiobook formats.

I'm looking for orange font on a white background as these are my brand colours.

Feel free to use some yellow and gold too if you deem it appropriate.

Title: Climb and Kindle
Subtitle: Find Your Voice. Tell Your Story. Share your Message.
Author: Owen Thistlewood

I would like to have a picture of a female speaker on the front cover.

Alternatively, some kind of image that symbolises public speaking like a microphone, podium etc

Target Market(s)

Aspiring professional speakers

Colors
f78f20

Requirements
Must have
• Correct spelling!
Nice to have
• A logo or picture that fits the theme, but no pressure if you can't think of anything
Should not have
• No men in suits please. I don't want this to have a 1980s corporate look.

```html
<!DOCTYPE html>
<html lang="en">
<head>
<meta charset="utf-8">
<title>Climb and Kindle – Book Cover</title>
<link rel="stylesheet" href="https://fonts.googleapis.com/css2?family=Raleway:wght@300;400;700;800;900&display=swap">
<style>
  :root {
    --page-bg: #ffffff;
    --cover-bg: #ffffff;
    --cover-edge: #e4e4e4;
    --orange-light: #fbb01b;
    --orange-deep: #f58220;
    --orange-text: #f78f20;
    --ink: #1e1e1e;
  }
  html, body {
    margin: 0;
    padding: 0;
    width: 1200px;
    height: 1200px;
    overflow: hidden;
    background: var(--page-bg);
  }
  .canvas {
    position: relative;
    width: 1200px;
    height: 1200px;
  }
  .book-cover {
    position: absolute;
    left: 360px;
    top: 240px;
    width: 480px;
    height: 719px;
    display: block;
  }
  .cover-bg {
    fill: var(--cover-bg);
    stroke: var(--cover-edge);
    stroke-width: 2px;
  }
  .title-word {
    font-family: "Raleway", Arial, sans-serif;
    font-weight: 900;
    text-transform: uppercase;
  }
  .title-word--kindle {
    stroke: var(--cover-bg);
    stroke-width: 6px;
    paint-order: stroke fill;
  }
  .title-joiner {
    font-family: "Raleway", Arial, sans-serif;
    font-weight: 800;
    font-size: 38px;
    letter-spacing: 2px;
    fill: var(--ink);
    stroke: var(--cover-bg);
    stroke-width: 6px;
    paint-order: stroke fill;
  }
  .subtitle {
    font-family: "Raleway", Arial, sans-serif;
    font-weight: 400;
    font-size: 20px;
    fill: var(--orange-text);
  }
  .author {
    font-family: "Raleway", Arial, sans-serif;
    font-weight: 800;
    font-size: 18px;
    fill: var(--ink);
  }
</style>
</head>
<body>
<main class="canvas">
  <svg class="book-cover" viewBox="0 0 480 719" xmlns="http://www.w3.org/2000/svg" aria-label="Climb and Kindle book cover">
    <defs>
      <linearGradient id="title-gradient" x1="0" y1="0" x2="0" y2="1">
        <stop offset="0" style="stop-color:#fbb01b"/>
        <stop offset="1" style="stop-color:#f58220"/>
      </linearGradient>
      <linearGradient id="arrow-gradient" gradientUnits="userSpaceOnUse" x1="0" y1="30" x2="0" y2="719">
        <stop offset="0" style="stop-color:#fbb01b"/>
        <stop offset="1" style="stop-color:#f58220"/>
      </linearGradient>
    </defs>

    <rect class="cover-bg" x="1" y="1" width="478" height="717"/>

    <!-- rising arrow -->
    <g class="rising-arrow" fill="url(#arrow-gradient)">
      <polygon points="195,30 229,89 161,89"/>
      <rect x="179.5" y="88" width="31" height="630"/>
    </g>

    <!-- title -->
    <g class="title" fill="url(#title-gradient)">
      <text class="title-word" x="20" y="291" font-size="190" textLength="150" lengthAdjust="spacingAndGlyphs">CL</text>
      <text class="title-word" x="218" y="291" font-size="190" textLength="244" lengthAdjust="spacingAndGlyphs">MB</text>
      <text class="title-joiner" x="222" y="343">AND</text>
      <text class="title-word title-word--kindle" x="22" y="458" font-size="130" textLength="436" lengthAdjust="spacingAndGlyphs">KINDLE</text>
    </g>

    <!-- subtitle -->
    <g class="subtitle-block">
      <text class="subtitle" x="226" y="532">FIND YOUR VOICE.</text>
      <text class="subtitle" x="226" y="568">TELL YOUR STORY.</text>
      <text class="subtitle" x="226" y="604">SHARE YOUR MESSAGE.</text>
    </g>

    <!-- author -->
    <text class="author" x="226" y="673" textLength="232" lengthAdjust="spacing">OWEN THISTLEWOOD</text>
  </svg>
</main>
</body>
</html>
```